Stonebridge Building and Projects business cards

A business card with watermark background (construction work)

Company logo attached

Home improvement projects
House renovations
Bathroom and kitchen renovations
House extensions
New builds and granny flats

Director Omar Haddani
(Phone number)
omar@sbpbuilding.com.au
(Instagram logo) sbp_building

```html
<!DOCTYPE html>
<html lang="en">
<head>
<meta charset="utf-8">
<title>Stonebridge Building and Projects – Business Cards</title>
<link rel="stylesheet" href="https://fonts.googleapis.com/css2?family=Roboto:wght@400;500;700&display=swap">
<style>
  :root {
    --blue: #1a78c2;
    --blue-dark: #1565a6;
    --ink: #2b2f33;
    --grey: #4a4f55;
    --paper: #ffffff;
    --paper-shade: #eef0f2;
    --backdrop: #e4e6e9;
  }
  * { box-sizing: border-box; margin: 0; padding: 0; }
  html, body { width: 1200px; height: 1050px; overflow: hidden; }
  body {
    background: var(--backdrop);
    font-family: "Roboto", Arial, sans-serif;
    color: var(--ink);
    position: relative;
  }
  .card {
    position: absolute;
    width: 700px;
    height: 400px;
    left: 250px;
    background: var(--paper);
    border-radius: 26px;
    overflow: hidden;
    box-shadow: 0 10px 30px rgba(0,0,0,.18);
  }
  .card--front { top: 70px; }
  .card--back { top: 560px; }

  /* Wordmark */
  .wordmark { position: absolute; text-align: center; }
  .wordmark__name {
    display: flex; align-items: center; gap: 10px;
    font-weight: 700; color: var(--blue);
    line-height: 1.1;
  }
  .wordmark__square { width: 16px; height: 16px; background: var(--blue); flex: none; }
  .wordmark__rule { height: 2px; background: var(--blue); margin: 8px 0 6px; }
  .wordmark__tagline { font-weight: 500; color: var(--blue); }

  /* Front */
  .watermark {
    position: absolute; left: 60px; top: 20px; width: 480px; height: 320px;
    background: radial-gradient(ellipse at center, rgba(200,205,210,.35), rgba(255,255,255,0) 70%);
  }
  .card--front .wordmark { left: 0; right: 0; top: 78px; display: flex; flex-direction: column; align-items: center; }
  .card--front .wordmark__name { font-size: 34px; }
  .card--front .wordmark__rule { width: 420px; }
  .card--front .wordmark__tagline { font-size: 22px; }
  .services {
    position: absolute; left: 0; right: 0; top: 222px; height: 84px;
    background: var(--blue);
    color: #fff; font-size: 18px; text-align: center;
    display: flex; flex-direction: column; justify-content: center; gap: 6px;
  }
  .services span.sep { margin: 0 8px; }
  .socials {
    position: absolute; left: 0; right: 0; top: 330px;
    display: flex; justify-content: center; gap: 50px;
    font-size: 16px; color: var(--grey);
  }

  .contact { display: flex; align-items: center; gap: 10px; }
  .icon { width: 18px; height: 18px; flex: none; }

  /* Back */
  .side-tab {
    position: absolute; left: -22px; top: 186px; width: 44px; height: 64px;
    border-radius: 0 32px 32px 0; background: var(--blue);
  }
  .card--back .wordmark { right: 48px; top: 58px; width: 330px; display: flex; flex-direction: column; align-items: flex-end; }
  .card--back .wordmark__name { font-size: 27px; }
  .card--back .wordmark__rule { width: 100%; }
  .card--back .wordmark__tagline { font-size: 19px; }
  .person { position: absolute; left: 56px; top: 140px; }
  .person__name { font-size: 26px; font-weight: 700; color: var(--blue); }
  .person__title { font-size: 16px; color: var(--grey); margin-top: 4px; }
  .contacts-left { position: absolute; left: 56px; top: 296px; display: flex; flex-direction: column; gap: 10px; font-size: 17px; color: var(--grey); }
  .contacts-right { position: absolute; left: 340px; top: 226px; display: flex; flex-direction: column; gap: 10px; font-size: 17px; color: var(--grey); }
  .base-stripe { position: absolute; left: 0; bottom: 0; width: 700px; height: 40px; }
</style>
</head>
<body>

<section class="card card--front" aria-label="Business card front">
  <div class="watermark" role="img" aria-label="Faint construction work watermark"></div>
  <div class="wordmark">
    <div class="wordmark__name"><span class="wordmark__square"></span>Stonebridge Building and Projects</div>
    <div class="wordmark__rule"></div>
    <div class="wordmark__tagline">Built right, first time!</div>
  </div>
  <div class="services">
    <p>Home Improvement Projects<span class="sep">|</span>House Renovations<span class="sep">|</span>House Extensions</p>
    <p>Bathroom &amp; Kitchen Renovations<span class="sep">|</span>New Builds &amp; Granny Flats</p>
  </div>
  <div class="socials">
    <div class="contact">
      <svg class="icon" viewBox="0 0 18 18"><circle cx="9" cy="9" r="8" fill="var(--blue)"/></svg>
      sbp_building
    </div>
    <div class="contact">
      <svg class="icon" viewBox="0 0 18 18" fill="none" stroke="var(--blue)" stroke-width="1.6"><circle cx="9" cy="9" r="7.5"/><ellipse cx="9" cy="9" rx="3.2" ry="7.5"/><path d="M1.5 9h15"/></svg>
      sbpbuilding.com.au
    </div>
  </div>
</section>

<section class="card card--back" aria-label="Business card back">
  <div class="side-tab"></div>
  <div class="wordmark">
    <div class="wordmark__name"><span class="wordmark__square"></span>Stonebridge Building and Projects</div>
    <div class="wordmark__rule"></div>
    <div class="wordmark__tagline">Built right, first time!</div>
  </div>
  <div class="person">
    <h1 class="person__name">Omar Haddani</h1>
    <p class="person__title">Managing Director</p>
  </div>
  <div class="contacts-right">
    <div class="contact">
      <svg class="icon" viewBox="0 0 18 18" fill="none" stroke="var(--blue)" stroke-width="1.6"><rect x="1.5" y="3.5" width="15" height="11" rx="1"/><path d="M1.5 4l7.5 6 7.5-6"/></svg>
      omar@sbpbuilding.com.au
    </div>
    <div class="contact">
      <svg class="icon" viewBox="0 0 18 18"><circle cx="9" cy="9" r="8" fill="var(--blue)"/><path d="M1 9h16M9 1c-3 3-3 13 0 16M9 1c3 3 3 13 0 16" stroke="#fff" stroke-width="1.2" fill="none"/></svg>
      www.sbpbuilding.com.au
    </div>
  </div>
  <div class="contacts-left">
    <div class="contact">
      <svg class="icon" viewBox="0 0 18 18" fill="none" stroke="var(--blue)" stroke-width="1.6"><circle cx="9" cy="9" r="7.5"/><path d="M6.3 5.2l1.4 1.6-.8 1.3c.6 1.2 1.5 2.1 2.7 2.7l1.3-.8 1.6 1.4-.9 1.4c-3-.4-5.3-2.7-5.8-5.8z" fill="var(--blue)" stroke="none"/></svg>
      0412 555 018
    </div>
    <div class="contact">
      <svg class="icon" viewBox="0 0 18 18"><circle cx="9" cy="9" r="8" fill="var(--blue)"/></svg>
      sbp_building
    </div>
  </div>
  <svg class="base-stripe" viewBox="0 0 700 40" preserveAspectRatio="none" aria-hidden="true">
    <polygon points="0,28 470,28 430,40 0,40" fill="var(--blue)"/>
    <polygon points="470,14 700,14 700,40 430,40" fill="var(--grey)"/>
  </svg>
</section>

</body>
</html>
```